Brightmill Data Works

Our company is about IT hardwares and IT solutions. IT hardware such as PC, RAMS, storage and servers. IT solutions such as project management, BA. We are also selling new technology too.

Target Market(s)

Consumer, Small to Medium Business, Corporate

Requirements
Must have
• The business card must have the following:
• Name:
• Title:
• Contact Number:
• Email address:
• Website:
• Color: Must match the logo color upgrade

```html
<!DOCTYPE html>
<html lang="en">
<head>
<meta charset="utf-8">
<title>Brightmill Data Works — Business Card</title>
<link rel="stylesheet" href="https://fonts.googleapis.com/css2?family=Dosis:wght@400;500;600&family=Exo+2:wght@700&family=Montserrat:wght@500&display=swap">
<style>
  :root {
    --backdrop: #d8d3ca;
    --paper: #fbfbfb;
    --charcoal: #424242;
    --charcoal-edge: #353535;
    --ink: #4a4a4a;
    --ink-soft: #5a5a5a;
    --amber: #e0962c;
    --white: #ffffff;
  }
  * { box-sizing: border-box; margin: 0; padding: 0; }
  html, body {
    width: 1200px;
    height: 950px;
    overflow: hidden;
    background: var(--backdrop);
  }
  .canvas {
    position: relative;
    width: 1200px;
    height: 950px;
  }
  .card {
    position: absolute;
    box-shadow: 0 6px 18px rgba(0, 0, 0, 0.22);
  }

  /* Front: personal details */
  .card-front {
    left: 70px;
    top: 200px;
    width: 600px;
    height: 343px;
    background: var(--paper);
    display: flex;
    align-items: center;
    justify-content: center;
  }
  .contact-block {
    font-family: "Dosis", sans-serif;
    color: var(--ink);
    transform: translateX(40px);
  }
  .brand-tag {
    display: flex;
    align-items: center;
    gap: 8px;
    font-family: "Dosis", sans-serif;
    font-weight: 600;
    font-size: 15px;
    letter-spacing: 1px;
    color: var(--amber);
    text-transform: uppercase;
    margin-bottom: 12px;
  }
  .brand-square {
    width: 14px;
    height: 14px;
    background: var(--amber);
  }
  .person-name {
    font-weight: 500;
    font-size: 30px;
    letter-spacing: 0.5px;
    line-height: 1;
    text-transform: uppercase;
  }
  .person-title {
    font-weight: 500;
    font-size: 19px;
    color: var(--amber);
    text-transform: uppercase;
    margin-top: 4px;
    margin-bottom: 18px;
  }
  .contact-line {
    font-weight: 500;
    font-size: 16px;
    color: var(--ink-soft);
    line-height: 1.45;
  }
  .contact-line .divider { margin: 0 4px; }
  .contact-web { font-weight: 600; }

  /* Back: brand side */
  .card-back {
    left: 770px;
    top: 185px;
    width: 343px;
    height: 600px;
    background: var(--charcoal);
    overflow: hidden;
  }
  .brand-lockup {
    position: absolute;
    top: 230px;
    left: 0;
    right: 0;
    display: flex;
    flex-direction: column;
    align-items: center;
    gap: 14px;
  }
  .brand-lockup .brand-square {
    width: 26px;
    height: 26px;
  }
  .brand-name {
    font-family: "Exo 2", sans-serif;
    font-weight: 700;
    font-size: 27px;
    line-height: 1.1;
    letter-spacing: 1px;
    text-align: center;
    text-transform: uppercase;
    color: var(--white);
  }
  .web-band {
    position: absolute;
    left: 0;
    right: 0;
    bottom: 70px;
    height: 42px;
    background: var(--amber);
    display: flex;
    align-items: center;
    justify-content: center;
    font-family: "Montserrat", sans-serif;
    font-weight: 500;
    font-size: 13px;
    letter-spacing: 3px;
    color: var(--white);
  }
</style>
</head>
<body>
<main class="canvas">

  <section class="card card-front" aria-label="Business card front">
    <div class="contact-block">
      <div class="brand-tag"><span class="brand-square"></span>Brightmill Data Works</div>
      <h1 class="person-name">Daniel Reyes</h1>
      <p class="person-title">CEO/Founder</p>
      <p class="contact-line">555 210 4476<span class="divider">|</span>daniel@brightmilldata.com</p>
      <p class="contact-line contact-web">www.brightmilldata.com</p>
    </div>
  </section>

  <section class="card card-back" aria-label="Business card back">
    <div class="brand-lockup">
      <span class="brand-square"></span>
      <p class="brand-name">Brightmill<br>Data Works</p>
    </div>
    <div class="web-band">www.brightmilldata.com</div>
  </section>

</main>
</body>
</html>
```